Pebble Tracks - explore habits of productive people

Pebble Tracks is a social place around habits and productivity

The full brief below:

https://notes.brimwellpad.net/page/d/7Qx-RtVmPLa93KwBz-H-cNmq2YeTsRfvUdGkHpXwaB/view?mode=shared

Colors

Designer to choose colors to be used in the design.

Requirements
Must have
• - a feed page to display habits
• - a habit page to add a habit
• / clean, no cluttered design, lots of white space
• / inspired by material design or other design system
Nice to have
• - user page

```html
<!DOCTYPE html>
<html lang="en">
<head>
<meta charset="utf-8">
<title>Pebble Tracks – Our Feed</title>
<link href="https://fonts.googleapis.com/css2?family=Roboto:wght@400;500;700&display=swap" rel="stylesheet">
<style>
:root{
  --brand:#2196f3;
  --page:#eef0f3;
  --surface:#ffffff;
  --line:#e3e6ea;
  --ink:#2b2f33;
  --ink-soft:#6b7178;
  --ink-faint:#9aa0a6;
  --link:#2196f3;
  --photo-a:#c9c2b6;
  --photo-b:#8d8478;
  --avatar:#a88e7a;
  --footer:#e4e7eb;
}
*{box-sizing:border-box;margin:0;padding:0}
html,body{width:678px;height:1200px;overflow:hidden}
body{font-family:"Roboto",sans-serif;background:var(--page);color:var(--ink);position:relative}

.topbar{position:absolute;left:0;top:0;width:678px;height:44px;background:var(--brand);display:flex;align-items:center;padding:0 18px 0 14px;color:#fff}
.brand-name{font-size:19px;font-weight:700;letter-spacing:.3px}
.topbar-actions{margin-left:auto;display:flex;align-items:center;gap:14px;font-size:12px}
.topbar .avatar{width:28px;height:28px;border:2px solid #fff}
.user-name{display:flex;align-items:center;gap:4px}
.add-link{font-weight:500}

.sidebar{position:absolute;left:0;top:44px;width:168px;height:1122px;background:var(--surface);border-right:1px solid var(--line)}
.nav-item{display:flex;align-items:center;gap:12px;height:32px;padding:0 16px;font-size:12.5px;color:var(--ink);border-bottom:1px solid var(--line)}
.nav-item svg{width:14px;height:14px;stroke:var(--ink-soft);fill:none;stroke-width:1.6}

.feed{position:absolute;left:178px;top:44px;width:484px;display:flex;flex-direction:column;gap:12px}
.feed-title{font-size:19px;font-weight:500;color:var(--ink);margin-top:14px;line-height:23px}
.search{height:24px;margin-top:-2px;background:var(--surface);border:1px solid var(--line);border-radius:2px;font-size:10px;color:var(--ink-faint);padding:0 8px;display:flex;align-items:center}

.card{width:484px;background:var(--surface);border:1px solid var(--line);border-radius:2px;box-shadow:0 1px 2px rgba(0,0,0,.05);padding:12px 16px 2px}

.post-head{display:flex;align-items:flex-start;gap:9px;position:relative}
.avatar{width:30px;height:30px;border-radius:50%;background:var(--avatar);flex:none}
.avatar.sm{width:22px;height:22px}
.author{font-size:11.5px;font-weight:500;color:var(--ink)}
.author-meta{font-size:9px;color:var(--ink-faint);margin-top:2px}
.close{position:absolute;right:0;top:0;font-size:13px;color:var(--ink-soft);line-height:1}
.time{font-size:9px;color:var(--ink-faint);margin:7px 0 5px}
.post-title{font-size:14px;font-weight:400;color:var(--ink);line-height:1.3;margin-bottom:7px}
.post-text{font-size:9.5px;line-height:1.5;color:var(--ink-soft)}
.read-more{color:var(--link)}

.post-inner{margin-top:10px}
.photos{display:flex;gap:8px;margin:2px 0 9px}
.photo{flex:1;height:130px;background:linear-gradient(135deg,var(--photo-a),var(--photo-b))}
.photo.alt{background:linear-gradient(135deg,#d8d3cc,#7d7f7a)}

.actions{display:flex;align-items:center;gap:6px;font-size:9.5px;color:var(--ink-soft);height:30px;border-bottom:1px solid var(--line);margin-top:6px}
.actions svg{width:11px;height:11px;fill:var(--ink-soft)}
.actions .sep{color:var(--line)}
.actions .share{margin-left:auto}
.comment-row{display:flex;align-items:center;gap:10px;height:34px}
.comment-input{flex:1;font-size:9.5px;color:var(--ink-faint);border-bottom:1px solid var(--line);padding-bottom:3px}

.footer{position:absolute;left:168px;top:1166px;width:510px;height:34px;background:var(--footer);font-size:10px;color:var(--ink-soft);display:flex;align-items:center;justify-content:center}
.footer .chat{position:absolute;right:16px;width:14px;height:14px;stroke:var(--ink-soft);fill:none;stroke-width:1.6}
</style>
</head>
<body>

<header class="topbar">
  <span class="brand-name">Pebble Tracks</span>
  <div class="topbar-actions">
    <svg width="16" height="14" viewBox="0 0 16 14"><rect x="1" y="2" width="14" height="10" rx="1" fill="none" stroke="#fff" stroke-width="1.5"/><path d="M1 3l7 5 7-5" fill="none" stroke="#fff" stroke-width="1.5"/><circle cx="14" cy="2" r="2.5" fill="#ffc107"/></svg>
    <div class="avatar" role="img" aria-label="Profile photo of Arlo"></div>
    <span class="user-name">Arlo <svg width="8" height="6" viewBox="0 0 8 6"><path d="M0 0h8L4 6z" fill="#fff"/></svg></span>
    <span class="add-link">+ Add</span>
  </div>
</header>

<nav class="sidebar">
  <div class="nav-item"><svg viewBox="0 0 16 16"><path d="M2 8l6-6 6 6M4 7v7h8V7"/></svg>Home</div>
  <div class="nav-item"><svg viewBox="0 0 16 16"><rect x="2" y="3" width="12" height="11"/><path d="M2 6h12M5 1v3M11 1v3"/></svg>Events</div>
  <div class="nav-item"><svg viewBox="0 0 16 16"><circle cx="8" cy="8" r="6"/><path d="M8 7v4M8 5v.5"/></svg>About Us</div>
  <div class="nav-item"><svg viewBox="0 0 16 16"><circle cx="6" cy="6" r="2.5"/><path d="M1 14c0-3 2-5 5-5s5 2 5 5M11 4a2.5 2.5 0 010 5M13 10c1 1 2 2 2 4"/></svg>Friends</div>
  <div class="nav-item"><svg viewBox="0 0 16 16"><path d="M3 8l3 3 7-7"/></svg>Habits</div>
  <div class="nav-item"><svg viewBox="0 0 16 16"><rect x="1" y="3" width="14" height="10"/><path d="M6 6v4l4-2z"/></svg>Videos</div>
  <div class="nav-item"><svg viewBox="0 0 16 16"><path d="M3 3a10 10 0 0110 10M3 7a6 6 0 016 6"/><circle cx="4" cy="12" r="1"/></svg>Feed</div>
</nav>

<main class="feed">
  <h1 class="feed-title">Our Feed</h1>
  <div class="search">Enter a keyword</div>

  <article class="card">
    <div class="post-head">
      <div class="avatar" role="img" aria-label="Profile photo of Mira Solen"></div>
      <div><div class="author">Mira Solen</div><div class="author-meta">Reviews (15) | Followers (15)</div></div>
      <span class="close">×</span>
    </div>
    <div class="time">5 minutes ago</div>
    <h2 class="post-title">After I pour my morning cup of coffee, I will meditate for sixty seconds.</h2>
    <p class="post-text">No matter how you use this strategy, the secret to creating a successful habit stack is selecting the right cue to kick things off. Unlike an implementation intention, which specifically states the time and location for a given behavior, habit stacking implicitly has the time and location built into it. When and where you choose to insert a habit into your daily routine can make a big difference. If you're trying to add meditation into your morning routine but mornings are chaotic and your kids keep running into the room, then that may <span class="read-more">Read More</span></p>
    <div class="actions">
      <svg viewBox="0 0 12 12"><path d="M1 5h2v6H1zM4 5l3-4c1 0 1.5.6 1.2 1.6L7.8 4H11v2l-1.5 5H4z"/></svg>Likes (15) <span class="sep">|</span>
      <svg viewBox="0 0 12 12"><path d="M11 7H9v-6h2zM8 7l-3 4c-1 0-1.5-.6-1.2-1.6L4.2 8H1V6l1.5-5H8z"/></svg>102 <span class="sep">|</span>
      <svg viewBox="0 0 12 12"><path d="M1 1h10v7H5l-3 3V8H1z"/></svg>Comments (80)
      <svg class="share" viewBox="0 0 12 12"><path d="M7 1l5 4-5 4V6.5C4 6.5 2 7.5 0 11c.5-4 2.5-7 7-7.5z"/></svg>
    </div>
    <div class="comment-row">
      <div class="avatar sm" role="img" aria-label="Your profile photo"></div>
      <div class="comment-input">Write a comment</div>
    </div>
  </article>

  <article class="card">
    <div class="post-head">
      <div class="avatar" role="img" aria-label="Profile photo of the sharing member"></div>
      <div><div class="author">Lorem ipsum dolor</div><div class="author-meta">Other subject location</div></div>
      <span class="close">×</span>
    </div>
    <div class="time">5 minutes ago</div>
    <h2 class="post-title">After I meditate for sixty seconds, I will write my to-do list for the day.</h2>
    <div class="post-inner">
      <div class="post-head">
        <div class="avatar" role="img" aria-label="Profile photo of Tova Reed"></div>
        <div><div class="author">Tova Reed</div><div class="author-meta">Reviews (15) | Followers (15)</div></div>
      </div>
      <div class="time">5 minutes ago</div>
      <div class="photos">
        <div class="photo" role="img" aria-label="Photo of a person meditating indoors"></div>
        <div class="photo alt" role="img" aria-label="Photo of a person sitting in a calm room"></div>
      </div>
      <p class="post-text">Overall, habit stacking allows you to create a set of simple rules that guide your future behavior. It's like you always have a game plan for which action should come next. Once you get comfortable with this approach, you can develop general habit stacks to guide you whenever the situation is appropriate <span class="read-more">Read More</span></p>
    </div>
    <div class="actions">
      <svg viewBox="0 0 12 12"><path d="M1 5h2v6H1zM4 5l3-4c1 0 1.5.6 1.2 1.6L7.8 4H11v2l-1.5 5H4z"/></svg>Likes (15) <span class="sep">|</span>
      <svg viewBox="0 0 12 12"><path d="M11 7H9v-6h2zM8 7l-3 4c-1 0-1.5-.6-1.2-1.6L4.2 8H1V6l1.5-5H8z"/></svg>102 <span class="sep">|</span>
      <svg viewBox="0 0 12 12"><path d="M1 1h10v7H5l-3 3V8H1z"/></svg>Comments (80)
      <svg class="share" viewBox="0 0 12 12"><path d="M7 1l5 4-5 4V6.5C4 6.5 2 7.5 0 11c.5-4 2.5-7 7-7.5z"/></svg>
    </div>
    <div class="comment-row">
      <div class="avatar sm" role="img" aria-label="Your profile photo"></div>
      <div class="comment-input">Write a comment</div>
    </div>
  </article>

  <article class="card">
    <div class="post-head">
      <div class="avatar" role="img" aria-label="Profile photo of Arlo Venn"></div>
      <div><div class="author">Arlo Venn</div><div class="author-meta">Reviews (15) | Followers (15)</div></div>
      <span class="close">×</span>
    </div>
    <div class="time">5 minutes ago</div>
    <h2 class="post-title">After I write my to-do list for the day, I will immediately begin my first task.</h2>
    <p class="post-text">You can also insert new behaviors into the middle of your current routines. For example, you may already have a morning routine that looks like this: Wake up &gt; Make my bed &gt; Take a shower. Let's say you want to develop the habit of reading more each night. You can expand your habit stack and try something like: Wake up &gt; Make my bed &gt; Place a book on my pillow &gt; Take a shower. Now, when you climb into bed each night, a book will be sitting there waiting for you to enjoy. <span class="read-more">Read More</span></p>
    <div class="actions">
      <svg viewBox="0 0 12 12"><path d="M1 5h2v6H1zM4 5l3-4c1 0 1.5.6 1.2 1.6L7.8 4H11v2l-1.5 5H4z"/></svg>Likes (15) <span class="sep">|</span>
      <svg viewBox="0 0 12 12"><path d="M11 7H9v-6h2zM8 7l-3 4c-1 0-1.5-.6-1.2-1.6L4.2 8H1V6l1.5-5H8z"/></svg>102 <span class="sep">|</span>
      <svg viewBox="0 0 12 12"><path d="M1 1h10v7H5l-3 3V8H1z"/></svg>Comments (80)
      <svg class="share" viewBox="0 0 12 12"><path d="M7 1l5 4-5 4V6.5C4 6.5 2 7.5 0 11c.5-4 2.5-7 7-7.5z"/></svg>
    </div>
    <div class="comment-row">
      <div class="avatar sm" role="img" aria-label="Your profile photo"></div>
      <div class="comment-input">Write a comment</div>
    </div>
  </article>
</main>

<footer class="footer">
  © 2018 Pebble Tracks. All rights reserved.
  <svg class="chat" viewBox="0 0 16 16"><path d="M2 2h12v9H7l-4 3v-3H2z"/></svg>
</footer>

</body>
</html>
```